Bluefinch Painting needs a Website

We need a website built for a Painting company I own, we mainly do residential painting, but don't want to be limited to that.

Need to have estimate request form.
Need pic's of past projects

I like the look of the website for http://www.harbor-brushworks.com
& "Westlake Home inspections"

My logo that was designed here on ArtHatch on the front page

I would like one of the houses I downloaded as part of the background
of the front page.

Target Market(s)

Home owners

Industry/Entity Type

Painting

Number of Pages Required

1 page

Font styles to use
Serif

Requirements
Must have
• Estimate request form for home owners to fill out -
• Name:
• Phone Number:
• Address:
• E-mail:
• Painting project description:
• And my info to:
• My phone number: (555) 318-7046
• My web address bluefinchpainting.example
Nice to have
• My logo that was designed here on ArtHatch

```html
<!DOCTYPE html>
<html lang="en">
<head>
<meta charset="utf-8">
<title>Bluefinch Painting</title>
<link href="https://fonts.googleapis.com/css2?family=Crimson+Text:wght@400;600&family=Arimo:wght@400;700&display=swap" rel="stylesheet">
<style>
:root{
  --blue:#1b7ac4;
  --ink:#222;
  --text:#333;
  --black:#111;
  --footer:#151515;
  --white:#fff;
}
*{box-sizing:border-box;margin:0;padding:0}
html,body{width:930px;height:1200px;overflow:hidden;background:var(--white)}
body{position:relative;font-family:"Arimo",Arial,sans-serif;color:var(--text)}
.abs{position:absolute}
.serif{font-family:"Crimson Text",Georgia,serif}

/* header */
.brand{left:124px;top:14px;display:flex;align-items:center;gap:10px}
.brand-mark{width:34px;height:34px;background:var(--blue)}
.brand-name{font-family:"Crimson Text",Georgia,serif;font-size:30px;color:var(--ink);letter-spacing:1px}
.truck-photo{left:503px;top:8px;width:151px;height:70px;background:linear-gradient(#f2f2f2,#d8d8d8);border:1px solid #bbb}
.estimate-btn{left:680px;top:3px;width:116px;height:22px;background:var(--blue);color:var(--white);font-size:13px;text-align:center;line-height:22px}
.call{left:683px;top:40px;display:flex;align-items:center;gap:6px}
.call small{display:block;font-size:10px;color:var(--ink)}
.call strong{display:block;font-size:15px;font-weight:400;color:var(--ink)}

/* nav */
.nav{left:0;top:78px;width:930px;height:31px;background:var(--blue);display:flex;padding-left:125px}
.nav a{font-family:"Crimson Text",Georgia,serif;font-size:13px;color:var(--white);text-decoration:none;line-height:31px;padding:0 14px;border-right:1px solid rgba(255,255,255,.3)}
.nav a.active{background:var(--black);font-weight:600}

/* hero */
.hero{left:0;top:109px;width:930px;height:308px;background:linear-gradient(#8fb6de 0%,#a8b4b6 35%,#8a8472 60%,#56643e 85%,#44512f 100%)}
.hero-caption{left:0;top:381px;width:930px;height:36px;background:rgba(40,40,40,.85);color:var(--white);font-size:18px;text-align:center;line-height:36px;letter-spacing:.3px}
.welcome{left:0;top:417px;width:930px;height:167px;background:linear-gradient(90deg,#8c8a86,#6f6d68 50%,#8a8985)}
.welcome-title{left:0;top:437px;width:930px;text-align:center;color:var(--white);font-size:17px}
.welcome-rule{left:340px;top:463px}
.welcome-text{left:140px;top:485px;width:650px;text-align:center;color:var(--white);font-size:9.5px;line-height:17px}
.welcome-btn{left:435px;top:545px;width:60px;height:19px;background:var(--black);color:var(--white);font-size:9.5px;text-align:center;line-height:19px}

/* content */
.col-title{font-size:17px;color:var(--ink);top:600px;font-weight:400}
.col-photo{top:633px;width:206px;height:131px;border:2px solid #ddd}
.col-text{top:770px;width:210px;font-size:9.5px;line-height:14.5px;color:var(--text)}
.btn{height:19px;background:var(--black);color:var(--white);font-size:9.5px;line-height:19px;text-align:center;padding:0 7px}
.inquiry-rule{left:607px;top:626px;width:203px;border-top:1px dashed #aaa}
.field{left:609px;width:198px;height:21px;border:1px solid #bbb;border-radius:2px;font-size:8.5px;font-style:italic;color:#666;padding:4px 8px}
.divider{left:133px;top:866px;width:675px;height:3px;background:radial-gradient(ellipse at center,#ddd,transparent 70%)}

/* gallery */
.gallery-icon{left:137px;top:885px;width:40px;height:40px;border:1px solid #ccc;border-radius:50%}
.gallery-title{left:186px;top:893px;font-size:17px;color:var(--ink);font-weight:400}
.arrow{top:899px;width:13px;height:13px}
.thumb{top:938px;width:120px;height:96px;border:1px solid #555;padding:3px;background:var(--white)}
.thumb-photo{width:100%;height:100%;position:relative}
.thumb-label{position:absolute;left:0;bottom:0;width:100%;height:18px;background:rgba(0,0,0,.7);color:var(--white);font-size:12px;line-height:18px;padding-left:6px}

/* footer */
.footer{left:0;top:1041px;width:930px;height:133px;background:var(--footer)}
.foot-h{top:1056px;font-size:9.5px;font-weight:700;color:var(--white);padding-bottom:4px;border-bottom:1px dashed #777}
.foot-list{font-size:9px;line-height:15.5px;color:#eee}
.accept{left:708px;top:1104px;font-size:9.5px;color:var(--white)}
.bottom{left:0;top:1174px;width:930px;height:26px;background:var(--blue);color:var(--white);font-size:9px;text-align:center;line-height:26px}
.card{width:21px;height:13px;border-radius:2px}
</style>
</head>
<body>

<header>
  <div class="abs brand"><span class="brand-mark"></span><span class="brand-name">Bluefinch Painting</span></div>
  <div class="abs truck-photo" role="img" aria-label="Company trailer with painted branding"></div>
  <div class="abs estimate-btn">Free Estimates</div>
  <div class="abs call">
    <svg width="24" height="24" viewBox="0 0 24 24"><circle cx="12" cy="12" r="10.5" fill="none" stroke="#1b7ac4" stroke-width="1.5"/><path d="M9 6c-2 1-2 4-1 7s3 5 6 5l1-2-2-1-1 1c-1-.5-2-2-2.5-3.5l1-1-1-2z" fill="#1b7ac4"/></svg>
    <div><small>Call Us Today</small><strong>555-318-7046</strong></div>
  </div>
</header>

<nav class="abs nav">
  <a class="active">Home</a><a>About Us</a><a>Exterior</a><a>Interior</a><a>Residential</a><a>Commerical</a><a>Past Projects</a><a style="border:none">Contact Us</a>
</nav>

<section>
  <div class="abs hero" role="img" aria-label="Two-storey family home with landscaped garden and flowering shrubs"></div>
  <div class="abs hero-caption serif">PROVIDING QUALITY WORK AT AFFORDABLE PRICES</div>
  <div class="abs welcome" role="img" aria-label="Company work trailers parked in a driveway, darkened"></div>
  <div class="abs welcome-title serif">Welcome to Bluefinch Painting</div>
  <svg class="abs welcome-rule" width="266" height="12" viewBox="0 0 266 12"><line x1="0" y1="3" x2="266" y2="3" stroke="#fff"/><line x1="0" y1="6" x2="266" y2="6" stroke="#fff"/><path d="M129 2l4 6 4-6" fill="none" stroke="#fff"/></svg>
  <p class="abs welcome-text">Lorem ipsum dolor sit amet, consectetuer adipiscing elit, sed diam nonummy nibh euismod &nbsp;rent ut laoreet dolore magna aliquam erat volutpat. Ut wisi enim ad minim veniam, quis nostrud lore xererci tation ullamcorper suscipit lobortis nisl ut aliquip ex ea commodo consequat. Duis autem revel eum iriure dolor in hendrerit in vulputate velit esse molestie consequat.</p>
  <svg class="abs" style="left:375px;top:549px" width="180" height="12"><line x1="0" y1="5" x2="180" y2="5" stroke="#fff"/><line x1="48" y1="2" x2="58" y2="2" stroke="#fff"/><line x1="48" y1="9" x2="58" y2="9" stroke="#fff"/><line x1="122" y1="2" x2="132" y2="2" stroke="#fff"/><line x1="122" y1="9" x2="132" y2="9" stroke="#fff"/></svg>
  <div class="abs welcome-btn">Read More</div>
</section>

<main>
  <h2 class="abs col-title serif" style="left:133px">Residential Painting</h2>
  <div class="abs col-photo" style="left:133px;background:linear-gradient(#5c7046,#a9a68a 55%,#6a675a)" role="img" aria-label="Painter on a ladder working on a house exterior"></div>
  <p class="abs col-text" style="left:134px">Sed ut perspiciatis unde omnis iste natus error sit voluptatem accusantium doloremque laudantium, totam rem aperiam.</p>
  <div class="abs btn" style="left:133px;top:819px">Read More</div>

  <h2 class="abs col-title serif" style="left:370px">Commerical Painting</h2>
  <div class="abs col-photo" style="left:370px;background:linear-gradient(#ebe9e4,#d4cfc4)" role="img" aria-label="Painter with roller painting an interior wall beside a ladder"></div>
  <p class="abs col-text" style="left:373px">Sed ut perspiciatis unde omnis iste natus error sit voluptatem accusantium doloremque laudantium, totam rem aperiam.</p>
  <div class="abs btn" style="left:373px;top:819px">Read More</div>

  <h2 class="abs col-title serif" style="left:607px">Quick Inquiry</h2>
  <div class="abs inquiry-rule"></div>
  <form>
    <div class="abs field" style="top:637px">Name</div>
    <div class="abs field" style="top:665px">Email</div>
    <div class="abs field" style="top:694px">Phone</div>
    <div class="abs field" style="top:722px">Type of Work</div>
    <div class="abs field" style="top:753px;height:59px">Message</div>
    <div class="abs btn" style="left:613px;top:819px;width:61px;font-weight:700">Submit</div>
  </form>

  <div class="abs divider"></div>

  <div class="abs gallery-icon"><svg width="40" height="40" viewBox="0 0 40 40"><rect x="12" y="14" width="14" height="13" fill="#1b7ac4"/><rect x="15" y="11" width="14" height="13" fill="none" stroke="#1b7ac4" stroke-width="1.5"/><circle cx="19" cy="20" r="2" fill="#fff"/></svg></div>
  <h2 class="abs gallery-title serif">Our Work Gallery</h2>
  <svg class="abs arrow" style="left:771px" viewBox="0 0 13 13"><rect width="13" height="13" fill="#111"/><path d="M8 3L4.5 6.5 8 10" stroke="#fff" stroke-width="2" fill="none"/></svg>
  <svg class="abs arrow" style="left:787px" viewBox="0 0 13 13"><rect width="13" height="13" fill="#1b7ac4"/><path d="M5 3l3.5 3.5L5 10" stroke="#fff" stroke-width="2" fill="none"/></svg>

  <div class="abs thumb" style="left:139px"><div class="thumb-photo" role="img" aria-label="Exterior painting project: house with garden" style="background:linear-gradient(#7aa8d8,#857b68 55%,#4b6236)"><span class="thumb-label serif">Exterior Painting 1</span></div></div>
  <div class="abs thumb" style="left:273px"><div class="thumb-photo" role="img" aria-label="Exterior painting project: painter on gable siding" style="background:linear-gradient(#6b8fc2,#b9bcc4 50%,#8c919a)"><span class="thumb-label serif">Exterior Painting 2</span></div></div>
  <div class="abs thumb" style="left:407px"><div class="thumb-photo" role="img" aria-label="Exterior painting project: painter rolling a wall" style="background:linear-gradient(#e2d7a8,#cfc18a)"><span class="thumb-label serif">Exterior Painting 3</span></div></div>
  <div class="abs thumb" style="left:541px"><div class="thumb-photo" role="img" aria-label="Exterior painting project: stucco home with lawn" style="background:linear-gradient(#8fb6dc,#c9b99a 50%,#5a8a3e)"><span class="thumb-label serif">Exterior Painting 4</span></div></div>
  <div class="abs thumb" style="left:675px"><div class="thumb-photo" role="img" aria-label="Exterior painting project: home with covered porch" style="background:linear-gradient(#a7b3bf,#7b7566 55%,#4a4a40)"><span class="thumb-label serif">Exterior Painting 5</span></div></div>
</main>

<footer>
  <div class="abs footer"></div>
  <div class="abs foot-h" style="left:133px">Quick Links</div>
  <ul class="abs foot-list" style="left:133px;top:1079px;list-style:none">
    <li>• Home</li><li>• About Us</li><li>• Services</li><li>• Past Projects</li><li>• Contact Us</li>
  </ul>

  <div class="abs foot-h" style="left:290px">Contact Information</div>
  <div class="abs foot-list" style="left:291px;top:1076px;width:180px">
    <div style="display:flex;gap:12px"><b>A:</b><span style="line-height:13.5px">Bluefinch Painting<br>Street Name City Name<br>State Zipcode</span></div>
    <div style="display:flex;gap:12px;margin-top:8px"><b>P:</b><span>555-318-7046</span></div>
    <div style="display:flex;gap:12px;margin-top:3px"><b>E:</b><span>inquiry@bluefinchpainting.example</span></div>
  </div>

  <div class="abs foot-h" style="left:472px">Work Times</div>
  <div class="abs foot-list" style="left:473px;top:1081px;line-height:22px">
    <div>◘ &nbsp;Our work timings are:</div>
    <div>◷ &nbsp;Monday - Friday. 8AM - 8PM</div>
    <div>◷ &nbsp;Saturday:9AM - 4PM</div>
    <div>◷ &nbsp;Sunday: closed</div>
  </div>

  <div class="abs" style="left:661px;top:1070px;display:flex;align-items:center;gap:6px">
    <span style="width:16px;height:16px;background:#ddd;display:block"></span>
    <span class="serif" style="font-size:15px;color:#ddd">Bluefinch Painting</span>
  </div>
  <div class="abs accept">We Accept</div>
  <div class="abs" style="left:673px;top:1121px;display:flex;gap:3px">
    <span class="card" style="background:#2a5fa8"></span>
    <span class="card" style="background:#eee"></span>
    <span class="card" style="background:#1a3e8c"></span>
    <span class="card" style="background:#3a8fd0"></span>
    <span class="card" style="background:#d93a2b"></span>
  </div>

  <div class="abs bottom">Copyright ©2015, BluefinchPainting &nbsp;All Rights Reserved</div>
</footer>

</body>
</html>
```